Quorvix banner ad for roofing company

We need an ad created for a Quorvix banner advertising campaign for a UK based roofing company.

The design should have a large photograph on the background (see attached).
The design should have our Glimmerdew rating (5 stars).
There should be a large text header at the top which reads "Your local roofing experts"

The following services should be listed:
- New roofs
- General roof repairs
- Drone surveys
- Single ply roofing
- Steel cladding
- Asbestos removal

The company logo needs to be visible (attached). Also the company telephone number 020 7946 0321 and website www.brinthoveroofing.com

The advert needs to be horizontal/landscape design. For full spec, please see here: https://promo.quorvix.com/advertiser-help/guides/ad-formats/single-photo-ads

Size required: 1.91:1 - 1200 x 628 pixels

```html
<!DOCTYPE html>
<html lang="en">
<head>
<meta charset="utf-8">
<title>Brinthove Roofing – Your Local Roofing Experts</title>
<link rel="stylesheet" href="https://fonts.googleapis.com/css2?family=Montserrat:ital,wght@0,700;1,800&family=Roboto:wght@400;500;700&display=swap">
<style>
  :root {
    --tint-top: #505c78;
    --tint-mid: #414c68;
    --tint-bottom: #333d58;
    --headline: #e4e7ee;
    --panel: rgba(236, 239, 245, 0.82);
    --panel-text: #2b3246;
    --white: #ffffff;
    --rating-green: #00b67a;
    --divider: rgba(255, 255, 255, 0.85);
  }
  * { margin: 0; padding: 0; box-sizing: border-box; }
  html, body { width: 1200px; height: 628px; overflow: hidden; background: var(--tint-bottom); }
  .banner {
    position: relative;
    width: 1200px;
    height: 628px;
    overflow: hidden;
    font-family: "Roboto", Arial, sans-serif;
  }
  .banner__photo {
    position: absolute;
    inset: 0;
    background:
      radial-gradient(ellipse at 85% 20%, rgba(120, 135, 160, 0.35), transparent 55%),
      radial-gradient(ellipse at 30% 60%, rgba(90, 110, 95, 0.25), transparent 60%),
      linear-gradient(180deg, var(--tint-top) 0%, var(--tint-mid) 55%, var(--tint-bottom) 100%);
  }
  .headline {
    position: absolute;
    left: 74px;
    top: 92px;
    font-family: "Montserrat", Arial, sans-serif;
    font-weight: 800;
    font-style: italic;
    font-size: 82px;
    line-height: 106px;
    letter-spacing: 0.5px;
    color: var(--headline);
  }
  .services { list-style: none; }
  .services__row {
    position: absolute;
    right: 0;
    height: 54px;
    background: var(--panel);
    color: var(--panel-text);
    font-size: 24px;
    line-height: 54px;
    padding-left: 40px;
    padding-right: 62px;
    white-space: nowrap;
  }
  .services__row:nth-child(1) { top: 175px; width: 498px; }
  .services__row:nth-child(2) { top: 250px; width: 517px; padding-left: 42px; }
  .services__row:nth-child(3) { top: 324px; width: 520px; padding-left: 41px; }
  .services__sep { margin: 0 10px; }
  .footer { position: absolute; left: 0; right: 0; top: 530px; height: 80px; }
  .brand {
    position: absolute;
    left: 44px;
    top: 12px;
    display: flex;
    align-items: center;
    gap: 12px;
    color: var(--white);
    font-family: "Montserrat", Arial, sans-serif;
    font-weight: 700;
    font-size: 40px;
    letter-spacing: -1px;
  }
  .brand__dot {
    width: 54px; height: 54px;
    border-radius: 50%;
    background: var(--white);
  }
  .divider {
    position: absolute;
    top: 4px;
    width: 2px;
    height: 72px;
    background: var(--divider);
  }
  .divider--one { left: 494px; }
  .divider--two { left: 887px; }
  .rating { position: absolute; left: 529px; top: 6px; color: var(--white); }
  .rating__top { display: flex; align-items: center; gap: 26px; font-size: 23px; font-weight: 500; }
  .rating__stars { display: flex; gap: 4px; }
  .rating__stars svg { width: 31px; height: 31px; }
  .rating__count {
    margin-top: 10px;
    display: flex; align-items: center; gap: 8px;
    font-size: 20px; font-weight: 500;
  }
  .rating__mark { width: 22px; height: 22px; border-radius: 50%; background: var(--rating-green); }
  .contact { position: absolute; left: 924px; top: 8px; color: var(--white); font-weight: 700; }
  .contact__phone { display: flex; align-items: center; gap: 8px; font-size: 21px; letter-spacing: 0.5px; }
  .contact__phone svg { width: 17px; height: 17px; }
  .contact__web { margin-top: 12px; font-size: 20px; }
</style>
</head>
<body>
<main class="banner">
  <div class="banner__photo" role="img" aria-label="Aerial drone photograph of modern residential apartment blocks with flat roofs, trees and roads, tinted dark blue"></div>

  <h1 class="headline">Your Local<br>Roofing<br>Experts</h1>

  <ul class="services">
    <li class="services__row">New roofs<span class="services__sep">|</span>General roof repairs</li>
    <li class="services__row">Drone surveys<span class="services__sep">|</span>Single ply roofing</li>
    <li class="services__row">Steel cladding<span class="services__sep">|</span>Asbestos removal</li>
  </ul>

  <footer class="footer">
    <div class="brand"><span class="brand__dot"></span>brinthoveroofing</div>
    <span class="divider divider--one"></span>

    <div class="rating">
      <div class="rating__top">
        <span>Excellent</span>
        <span class="rating__stars" aria-label="5 out of 5 stars">
          <svg viewBox="0 0 24 24"><path fill="#00b67a" d="M12 1.5l3.1 6.9 7.4.7-5.6 5 1.7 7.4L12 17.6 5.4 21.5l1.7-7.4-5.6-5 7.4-.7z"/></svg>
          <svg viewBox="0 0 24 24"><path fill="#00b67a" d="M12 1.5l3.1 6.9 7.4.7-5.6 5 1.7 7.4L12 17.6 5.4 21.5l1.7-7.4-5.6-5 7.4-.7z"/></svg>
          <svg viewBox="0 0 24 24"><path fill="#00b67a" d="M12 1.5l3.1 6.9 7.4.7-5.6 5 1.7 7.4L12 17.6 5.4 21.5l1.7-7.4-5.6-5 7.4-.7z"/></svg>
          <svg viewBox="0 0 24 24"><path fill="#00b67a" d="M12 1.5l3.1 6.9 7.4.7-5.6 5 1.7 7.4L12 17.6 5.4 21.5l1.7-7.4-5.6-5 7.4-.7z"/></svg>
          <svg viewBox="0 0 24 24"><path fill="#00b67a" d="M12 1.5l3.1 6.9 7.4.7-5.6 5 1.7 7.4L12 17.6 5.4 21.5l1.7-7.4-5.6-5 7.4-.7z"/></svg>
        </span>
      </div>
      <div class="rating__count">39 reviews on <span class="rating__mark"></span> Glimmerdew</div>
    </div>

    <span class="divider divider--two"></span>

    <div class="contact">
      <div class="contact__phone">
        <svg viewBox="0 0 24 24" aria-hidden="true"><path fill="#ffffff" d="M6.6 10.8a15.1 15.1 0 006.6 6.6l2.2-2.2c.3-.3.7-.4 1-.2 1.1.4 2.3.6 3.6.6.6 0 1 .4 1 1V20c0 .6-.4 1-1 1A17 17 0 013 4c0-.6.4-1 1-1h3.5c.6 0 1 .4 1 1 0 1.3.2 2.5.6 3.6.1.3 0 .7-.2 1z"/></svg>
        (020) 7946 0321
      </div>
      <div class="contact__web">www.brinthoveroofing.com</div>
    </div>
  </footer>
</main>
</body>
</html>
```